Water ATM Card

Need a design for water ATM cards. Size of card is 3.375 x 2.125 inch
On the Front include the Cedar hollow Logo.
Bottom right corner should have Price $100
On the Back
This card is to be used to access water refills at any Cedar Hollow Water Vending Machines.
Please contact (869) 418 2930 or (869) 534 1276 or email clearflowbox@mailvista.example for any assistance or recharging of card.

```html
<!DOCTYPE html>
<html lang="en">
<head>
<meta charset="utf-8">
<title>Cedar Hollow Water Card</title>
<link rel="stylesheet" href="https://fonts.googleapis.com/css2?family=Montserrat:wght@400;500;700;800&display=swap">
<style>
:root{
  --stage:#1b1b1b;
  --card-blue:#1c4f9c;
  --card-blue-back:#2152a3;
  --brand-blue:#1e56a8;
  --brand-green:#3a9e45;
  --white:#ffffff;
  --faint:rgba(120,160,225,0.35);
}
*{margin:0;padding:0;box-sizing:border-box}
html,body{width:1200px;height:1059px;overflow:hidden;background:var(--stage);font-family:'Montserrat',sans-serif}
.canvas{position:relative;width:1200px;height:1059px}
.card{position:absolute;border-radius:18px;overflow:hidden;color:var(--white)}
.card--front{left:256px;top:87px;width:688px;height:393px;background:var(--card-blue)}
.card--back{left:253px;top:546px;width:694px;height:395px;background:var(--card-blue-back)}
.front-shape{position:absolute;inset:0}
.holder{position:absolute;left:38px;top:68px}
.holder__name{font-weight:700;font-size:24px;letter-spacing:.5px;line-height:1}
.holder__role{font-weight:400;font-size:14px;letter-spacing:.5px;margin-top:8px}
.contacts{position:absolute;left:38px;top:250px;list-style:none}
.contacts li{display:flex;align-items:center;height:24px;font-size:15px;letter-spacing:.2px}
.contacts li:nth-child(2){margin-top:4px}
.contacts svg{width:14px;height:14px;margin-right:8px;fill:var(--white);flex:none}
.brand-name{position:absolute;left:545px;top:196px;transform:translateX(-50%);white-space:nowrap;
  font-weight:800;font-size:21px;letter-spacing:.5px;color:var(--brand-blue)}
.price{position:absolute;left:545px;top:252px;transform:translateX(-50%);white-space:nowrap;
  font-weight:800;font-size:34px;color:var(--brand-green)}
.back-usage{position:absolute;left:50px;right:50px;top:58px;text-align:center;font-size:15px;line-height:1.5;letter-spacing:.2px}
.back-brand{position:absolute;left:0;right:0;top:196px;text-align:center;font-weight:800;
  font-size:44px;letter-spacing:1px;color:var(--faint)}
.back-note{position:absolute;left:0;right:0;top:286px;text-align:center;font-size:15px;line-height:26px;letter-spacing:.2px}
</style>
</head>
<body>
<main class="canvas">
  <section class="card card--front">
    <svg class="front-shape" viewBox="0 0 688 393" aria-hidden="true">
      <path d="M535 0 Q230 204 532 393 L688 393 L688 0 Z" fill="var(--white)"/>
      <path d="M532 14 Q262 204 530 390" fill="none" stroke="var(--brand-green)" stroke-width="3"/>
    </svg>
    <div class="holder">
      <p class="holder__name">DANIEL REYES</p>
      <p class="holder__role">OWER</p>
    </div>
    <ul class="contacts">
      <li><svg viewBox="0 0 24 24"><path d="M6.6 10.8a15.1 15.1 0 0 0 6.6 6.6l2.2-2.2c.3-.3.7-.4 1-.2 1.1.4 2.3.6 3.6.6.6 0 1 .4 1 1V20c0 .6-.4 1-1 1C10.6 21 3 13.4 3 4c0-.6.4-1 1-1h3.5c.6 0 1 .4 1 1 0 1.3.2 2.5.6 3.6.1.3 0 .7-.2 1z"/></svg>(869) 418 2930</li>
      <li><svg viewBox="0 0 24 24"><path d="M7 1h10a2 2 0 0 1 2 2v18a2 2 0 0 1-2 2H7a2 2 0 0 1-2-2V3a2 2 0 0 1 2-2zm0 3v14h10V4zm5 15.5a1.2 1.2 0 1 0 0 2.4 1.2 1.2 0 0 0 0-2.4z"/></svg>(869) 534 1276</li>
      <li><svg viewBox="0 0 24 24"><path d="M2 5h20v2l-10 6L2 7zm0 4.3 10 6 10-6V19H2z"/></svg>clearflowbox@mailvista.example</li>
      <li><svg viewBox="0 0 24 24"><path d="M12 2a10 10 0 1 0 0 20 10 10 0 0 0 0-20zm-1 17.9A8 8 0 0 1 4.2 10L9 15v1c0 1.1.9 2 2 2zm6.9-2.5A2 2 0 0 0 16 16h-1v-3c0-.6-.4-1-1-1H8v-2h2c.6 0 1-.4 1-1V7h2a2 2 0 0 0 2-2v-.4a8 8 0 0 1 2.9 12.8z"/></svg>www.websitename here.com</li>
    </ul>
    <p class="brand-name">CEDAR HOLLOW</p>
    <p class="price">Price $100</p>
  </section>

  <section class="card card--back">
    <p class="back-usage">This card is to be used to access water refills at any<br>Cedar Hollow Water Vending Machines.</p>
    <p class="back-brand">CEDAR HOLLOW</p>
    <p class="back-note">Please contact (869) 418 2930 or (869) 534 1276<br>or email clearflowbox@mailvista.example<br>for any assistance or recharging of card.</p>
  </section>
</main>
</body>
</html>
```